Roofing Contractor business card redesign

I want to redesign my business card with a fresh, eye catching concept

Target Market(s)

Residential Roofing Clients, potential employees, and subcontractors.

Industry/Entity Type

Business

Colors

Designer to choose colors to be used in the design.

Requirements
Nice to have
• I just want something that's more pleasing to the eye. You can use a combination of either / or of my logos.

```html
<!DOCTYPE html>
<html lang="en">
<head>
<meta charset="utf-8">
<title>Steady Hand Builders – Business Card</title>
<link href="https://fonts.googleapis.com/css2?family=Oswald:wght@500;600&family=Work+Sans:wght@300;400&display=swap" rel="stylesheet">
<style>
  :root {
    --bg: #2b2a29;
    --orange: #f28322;
    --brown: #4a1510;
    --white: #ffffff;
    --ink: #2b2320;
  }
  html, body {
    margin: 0;
    width: 1200px;
    height: 930px;
    overflow: hidden;
    background: var(--bg);
  }
  .card {
    position: absolute;
    left: 278px;
    width: 644px;
    height: 369px;
    border-radius: 22px;
    overflow: hidden;
    box-shadow: 0 10px 24px rgba(0,0,0,.45);
  }
  .card--front { top: 75px; background: var(--white); }
  .card--back { top: 486px; background: var(--orange); }

  .front-swoosh { position: absolute; inset: 0; width: 644px; height: 369px; }

  .brand-block {
    position: absolute;
    left: 78px;
    top: 100px;
    width: 160px;
    display: flex;
    align-items: center;
    gap: 10px;
  }
  .brand-dot {
    flex: none;
    width: 30px;
    height: 30px;
    border-radius: 50%;
    background: var(--orange);
  }
  .brand-name {
    font-family: "Oswald", sans-serif;
    font-weight: 600;
    color: var(--brown);
    font-size: 28px;
    line-height: 1.05;
    margin: 0;
  }

  .divider {
    position: absolute;
    left: 299px;
    top: 85px;
    width: 2px;
    height: 176px;
    background: var(--orange);
  }

  .contact {
    position: absolute;
    left: 351px;
    top: 80px;
    font-family: "Work Sans", sans-serif;
    font-weight: 300;
    color: var(--ink);
  }
  .contact__name {
    font-family: "Oswald", sans-serif;
    font-weight: 500;
    color: var(--orange);
    font-size: 29px;
    letter-spacing: 1px;
    line-height: 1;
    margin: 0 0 4px;
  }
  .contact__role { font-size: 15px; line-height: 18px; margin: 0; }
  .contact__address { font-size: 16px; line-height: 21px; margin: 6px 0 6px; font-style: normal; }
  .contact__list { list-style: none; margin: 0; padding: 0; font-size: 16px; line-height: 20.5px; }
  .contact__list li { display: flex; align-items: center; gap: 10px; }
  .contact__list svg { width: 12px; height: 12px; flex: none; }

  .back-brand {
    position: absolute;
    left: 0; right: 0;
    top: 118px;
    display: flex;
    flex-direction: column;
    align-items: center;
    font-family: "Oswald", sans-serif;
    font-weight: 600;
    color: var(--brown);
  }
  .back-brand__row { display: flex; align-items: center; gap: 16px; }
  .back-brand__mark {
    width: 72px; height: 72px; border-radius: 50%;
    background: var(--brown);
  }
  .back-brand__name { font-size: 64px; line-height: 1; margin: 0; }
  .back-brand__sub { font-size: 30px; line-height: 1; margin: 14px 0 0; }
</style>
</head>
<body>

<section class="card card--front">
  <svg class="front-swoosh" viewBox="0 0 644 369" aria-hidden="true">
    <path d="M230 340 C400 342 540 322 644 286 L644 369 L230 369 Z" fill="var(--orange)"/>
    <path d="M230 342 C400 344 540 324 644 310" fill="none" stroke="var(--white)" stroke-width="4"/>
    <path d="M138 329 C300 348 500 342 644 316 L644 369 L240 369 Z" fill="var(--brown)"/>
    <path d="M0 241 C80 300 180 350 245 369 L0 369 Z" fill="var(--orange)"/>
    <path d="M0 250 C80 305 175 350 230 369" fill="none" stroke="var(--white)" stroke-width="3"/>
  </svg>

  <div class="brand-block">
    <span class="brand-dot"></span>
    <p class="brand-name">Steady Hand Builders, Inc.</p>
  </div>

  <div class="divider"></div>

  <div class="contact">
    <h1 class="contact__name">DAN MERCER</h1>
    <p class="contact__role">Ridgeline Certified Roof Inspector</p>
    <p class="contact__role">Licensed Property Adjuster</p>
    <address class="contact__address">4810 Cedar Ridge Lane<br>Suite 110 Plano, TX 75024</address>
    <ul class="contact__list">
      <li><svg viewBox="0 0 12 12"><path d="M2.5 1 L4.5 1 L5 3.5 L3.8 4.5 C4.5 6 6 7.5 7.5 8.2 L8.5 7 L11 7.5 L11 9.5 C11 10.3 10.3 11 9.5 11 C5 10.6 1.4 7 1 2.5 C1 1.7 1.7 1 2.5 1 Z" fill="var(--orange)"/></svg>(555) 210-4000</li>
      <li><svg viewBox="0 0 12 12"><rect x="3" y="0.8" width="6.4" height="10.4" rx="1.2" fill="none" stroke="var(--orange)" stroke-width="1.3"/><circle cx="6.2" cy="9.2" r=".8" fill="var(--orange)"/></svg>(555) 318-7720</li>
      <li><svg viewBox="0 0 12 12"><rect x="1" y="2.5" width="10" height="7" fill="none" stroke="var(--orange)" stroke-width="1.2"/><path d="M1 2.5 L6 6.5 L11 2.5" fill="none" stroke="var(--orange)" stroke-width="1.2"/></svg>dan@steadyhandtx.com</li>
    </ul>
  </div>
</section>

<section class="card card--back">
  <div class="back-brand">
    <div class="back-brand__row">
      <span class="back-brand__mark"></span>
      <p class="back-brand__name">Steady Hand</p>
    </div>
    <p class="back-brand__sub">Builders, Inc.</p>
  </div>
</section>

</body>
</html>
```